New Zealand Marlborough Sauvignon Blanc wine packaging design

We need packaging design for our new wine brand, Dunmore Vale. The wine is a New Zealand Marlborough Sauvignon Blanc. We would like the packaging will portray elegance and style with an understated label. We are looking for a label that portrays the elegance of the French Riviera. The label should be round or pill shaped.
Updates

Industry/Entity Type

Wine

Font styles to use
Serif
Sans Serif

Requirements
Must have
• The words in order of importance: Dunmore Vale, Sauvignon Blanc, Marlborough, New Zealand. It should be fit to the bottle posted in the links
Nice to have
• a pill shape or circular shape
Should not have
• Illustrations of wine bottles, wine glasses, or grapes

```html
<!DOCTYPE html>
<html lang="en">
<head>
<meta charset="utf-8">
<title>Dunmore Vale Sauvignon Blanc – Label</title>
<link rel="stylesheet" href="https://fonts.googleapis.com/css2?family=Pinyon+Script&display=swap">
<style>
  :root {
    --canvas: #f2efb6;
    --label-outer: #faf8de;
    --label-wash: #f3f1c8;
    --label-inner: #ffffff;
    --rule: #c3c452;
    --ink: #7b7828;
    --floral: #d9dc8c;
    --floral-soft: #e6e8ad;
  }
  html, body {
    margin: 0;
    padding: 0;
    width: 1200px;
    height: 675px;
    overflow: hidden;
    background: var(--canvas);
  }
  .label-stage {
    display: block;
    width: 1200px;
    height: 675px;
  }
  .label-outer { fill: var(--label-outer); }
  .label-wash { fill: var(--label-wash); }
  .label-ring { fill: none; stroke: var(--rule); stroke-width: 0.8; }
  .label-inner { fill: var(--label-inner); stroke: var(--rule); stroke-width: 0.8; }
  .floral-area { fill: var(--floral); opacity: 0.55; }
  .floral-area--soft { fill: var(--floral-soft); opacity: 0.7; }
  .title-rule { stroke: var(--rule); stroke-width: 0.9; }
  .brand-name,
  .variety,
  .region {
    font-family: "Pinyon Script", cursive;
    fill: var(--ink);
  }
  .brand-name { font-size: 64px; }
  .variety { font-size: 34px; }
  .region { font-size: 27px; }
</style>
</head>
<body>
<svg class="label-stage" viewBox="0 0 1200 675" xmlns="http://www.w3.org/2000/svg">
  <defs>
    <clipPath id="label-disc">
      <circle cx="600" cy="337" r="300"/>
    </clipPath>
    <filter id="inner-shadow" x="-20%" y="-20%" width="140%" height="140%">
      <feDropShadow dx="0" dy="3" stdDeviation="9" flood-color="#8a8a40" flood-opacity="0.22"/>
    </filter>
    <filter id="soft-blur">
      <feGaussianBlur stdDeviation="6"/>
    </filter>
    <path id="region-arc" d="M 373 377 A 230 230 0 0 0 827 377"/>
  </defs>

  <g class="label" clip-path="url(#label-disc)">
    <circle class="label-outer" cx="600" cy="337" r="300"/>

    <g class="watercolour-wash" role="img" aria-label="Soft pale-green watercolour wash">
      <ellipse class="label-wash" cx="720" cy="150" rx="190" ry="110" filter="url(#soft-blur)"/>
      <ellipse class="label-wash" cx="860" cy="330" rx="70" ry="120" filter="url(#soft-blur)"/>
      <ellipse class="label-wash" cx="760" cy="560" rx="150" ry="60" filter="url(#soft-blur)"/>
    </g>

    <circle class="label-ring" cx="600" cy="337" r="252"/>
    <circle class="label-inner" cx="600" cy="337" r="204" filter="url(#inner-shadow)"/>

    <g class="floral-sprig floral-sprig--top" role="img" aria-label="Line drawing of blossoming flowers and buds">
      <ellipse class="floral-area--soft" cx="730" cy="170" rx="150" ry="80" transform="rotate(25 730 170)" filter="url(#soft-blur)"/>
      <ellipse class="floral-area" cx="700" cy="215" rx="70" ry="50" filter="url(#soft-blur)"/>
      <ellipse class="floral-area" cx="655" cy="120" rx="55" ry="35" filter="url(#soft-blur)"/>
    </g>
    <g class="floral-sprig floral-sprig--left" role="img" aria-label="Line drawing of blossoming flowers and leaves">
      <ellipse class="floral-area--soft" cx="430" cy="465" rx="130" ry="75" transform="rotate(-20 430 465)" filter="url(#soft-blur)"/>
      <ellipse class="floral-area" cx="420" cy="480" rx="60" ry="45" filter="url(#soft-blur)"/>
      <ellipse class="floral-area" cx="490" cy="420" rx="40" ry="30" filter="url(#soft-blur)"/>
    </g>
    <g class="floral-sprig floral-sprig--right" role="img" aria-label="Line drawing of bell flowers and buds">
      <ellipse class="floral-area--soft" cx="795" cy="445" rx="110" ry="60" transform="rotate(-30 795 445)" filter="url(#soft-blur)"/>
      <ellipse class="floral-area" cx="780" cy="435" rx="50" ry="35" filter="url(#soft-blur)"/>
    </g>
  </g>

  <g class="label-title">
    <text class="brand-name" x="600" y="328" text-anchor="middle">Dunmore Vale</text>
    <line class="title-rule" x1="417" y1="337" x2="783" y2="337"/>
    <text class="variety" x="600" y="376" text-anchor="middle">Sauvignon Blanc</text>
  </g>

  <text class="region">
    <textPath href="#region-arc" startOffset="50%" text-anchor="middle">Marlborough, New Zealand</textPath>
  </text>
</svg>
</body>
</html>
```